Medical VIP club - small design

Please read the specs in a design brief attached. Also we don't have logo in a Vector format and attaching the only version we have.

Club

```html
<!DOCTYPE html>
<html lang="en">
<head>
<meta charset="utf-8">
<title>Corvella — VIP Club</title>
<link rel="stylesheet" href="https://fonts.googleapis.com/css2?family=Arimo:wght@400;700&display=swap">
<style>
  :root {
    --header-brown: #7b6a4f;
    --header-dark: #5f4f38;
    --body-brown: #6a5a40;
    --tab-top: #b7a586;
    --tab-bottom: #6f5f44;
    --tab-olive-top: #c9c46a;
    --tab-olive-bottom: #8d8a3c;
    --tab-gold-top: #f0c93a;
    --tab-gold-bottom: #b68e12;
    --band-light: #f1e6d2;
    --band-mid: #d9c6a5;
    --title-top: #8c7e57;
    --title-bottom: #6a5c3b;
    --panel: #ffffff;
    --text: #4a4a4a;
    --rule: #e4e0da;
    --logo: #f3e7d0;
    --logo-dark: #6b5535;
  }
  * { margin: 0; padding: 0; box-sizing: border-box; }
  html, body { width: 1200px; height: 874px; overflow: hidden; }
  body {
    font-family: "Arimo", Arial, sans-serif;
    background: var(--body-brown);
    position: relative;
  }
  .site-header {
    position: absolute; left: 0; top: 0; width: 1200px; height: 279px;
    background: radial-gradient(ellipse at 50% 30%, var(--header-brown), var(--header-dark));
  }
  .brand {
    position: absolute; left: 40px; top: 84px;
    display: flex; align-items: center; gap: 14px;
    font-size: 54px; font-weight: 700; color: var(--logo);
    white-space: nowrap;
  }
  .brand-dot { width: 28px; height: 28px; border-radius: 50%; background: var(--logo); }
  .phone-block {
    position: absolute; left: 780px; top: 52px;
    display: flex; align-items: center; gap: 20px;
  }
  .phone-number {
    font-size: 40px; font-weight: 700; color: #ffffff; white-space: nowrap;
    text-shadow: 0 2px 4px rgba(0,0,0,.55);
  }
  .tab-band {
    position: absolute; left: 0; top: 241px; width: 1200px; height: 38px;
    background: linear-gradient(var(--band-light), var(--band-mid));
  }
  .main-nav { position: absolute; left: 24px; top: 206px; display: flex; gap: 3.6px; }
  .main-nav a {
    width: 190px; height: 73px; display: flex; align-items: center; justify-content: center;
    padding-top: 6px;
    border-radius: 16px 16px 0 0;
    background: linear-gradient(var(--tab-top), var(--tab-bottom));
    border: 2px solid #ead9ba; border-bottom: none;
    color: #ffffff; text-decoration: none; font-size: 20px; white-space: nowrap;
    text-shadow: 0 1px 2px rgba(0,0,0,.35);
  }
  .main-nav a.is-current { background: linear-gradient(var(--tab-olive-top), var(--tab-olive-bottom)); }
  .main-nav a.is-highlight { background: linear-gradient(var(--tab-gold-top), var(--tab-gold-bottom)); }
  .content-panel {
    position: absolute; left: 24px; top: 289px; width: 1158px; height: 485px;
    background: var(--panel); border: 1px solid #d8cfbf;
  }
  .panel-title {
    margin: 4px 4px 0; height: 55px; padding-left: 16px;
    display: flex; align-items: center;
    background: linear-gradient(var(--title-top), var(--title-bottom));
    border: 2px solid #ffffff; box-shadow: 0 2px 5px rgba(0,0,0,.3);
    color: #ffffff; font-size: 24px; font-weight: 400;
  }
  .entry { position: absolute; left: 18px; width: 1122px; display: flex; gap: 24px; }
  .entry-one { top: 84px; }
  .entry-two { top: 283px; }
  .entry-photo {
    flex: none; width: 154px; height: 141px;
    background: linear-gradient(160deg, #9fc6ea 0%, #f4f1ea 55%, #8a6a4a 100%);
    box-shadow: 2px 3px 5px rgba(0,0,0,.35);
  }
  .entry p { font-size: 14.3px; line-height: 22px; color: var(--text); margin-top: -4px; }
  .entry-rule { position: absolute; left: 18px; top: 253px; width: 1122px; border-top: 1px solid var(--rule); }
  .site-footer {
    position: absolute; left: 0; top: 784px; width: 1200px; height: 90px;
    background: linear-gradient(#ffffff, var(--band-light) 40%, var(--band-mid));
    border-top: 2px solid #c9b48f;
  }
  .social { position: absolute; left: 24px; top: 28px; display: flex; gap: 6px; }
  .social span { width: 37px; height: 37px; border-radius: 5px; box-shadow: 1px 2px 3px rgba(0,0,0,.3); }
  .social .s1 { background: #3b5b9a; }
  .social .s2 { background: #5cc4e8; }
  .social .s3 { background: #e8712b; }
  .copyright { position: absolute; left: 0; width: 1200px; top: 45px; text-align: center; font-size: 13px; color: #333; }
  .footer-brand {
    position: absolute; right: 26px; top: 26px;
    display: flex; align-items: center; gap: 8px;
    font-size: 32px; font-weight: 700; color: var(--logo-dark); white-space: nowrap;
  }
  .footer-brand .brand-dot { width: 16px; height: 16px; background: var(--logo-dark); }
</style>
</head>
<body>
<header class="site-header">
  <div class="brand"><span class="brand-dot"></span>Corvella</div>
  <div class="phone-block">
    <svg width="104" height="104" viewBox="0 0 104 104" aria-hidden="true">
      <defs>
        <radialGradient id="phoneBall" cx="40%" cy="30%" r="70%">
          <stop offset="0" stop-color="#e6c17a"/>
          <stop offset=".6" stop-color="#a06a22"/>
          <stop offset="1" stop-color="#5a3a10"/>
        </radialGradient>
      </defs>
      <circle cx="52" cy="52" r="50" fill="url(#phoneBall)" stroke="#d9c7a3" stroke-width="2"/>
      <path d="M26 44 Q52 26 78 44 L74 52 L64 48 L62 42 Q52 38 42 42 L40 48 L30 52 Z" fill="#fff"/>
      <path d="M36 56 L42 48 H62 L68 56 V74 H36 Z" fill="#fff"/>
      <circle cx="52" cy="62" r="6" fill="#a06a22"/>
    </svg>
    <span class="phone-number">416-555-0190</span>
  </div>
</header>

<div class="tab-band"></div>
<nav class="main-nav">
  <a href="#">About Us</a>
  <a href="#" class="is-current">VIP Club</a>
  <a href="#">Services</a>
  <a href="#">Packages &amp; Prices</a>
  <a href="#" class="is-highlight">Registration</a>
  <a href="#">Contacts</a>
</nav>

<main class="content-panel">
  <h1 class="panel-title">VIP Club</h1>
  <article class="entry entry-one">
    <div class="entry-photo" role="img" aria-label="Couple in white robes on a seaside terrace with arches"></div>
    <p>Lorem ipsum dolor sit amet consecutor. Lorem ipsum dolor sit amet consecutor. Lorem ipsum dolor sit amet consecutor. Lorem ipsum dolor sit amet consecutor. Lorem ipsum dolor sit amet consecutor. Lorem ipsum dolor sit amet consecutor. Lorem ipsum dolor sit amet consecutor. Lorem ipsum dolor sit amet consecutor. Lorem ipsum dolor sit amet consecutor. Lorem ipsum dolor sit amet consecutor. Lorem ipsum dolor sit amet consecutor. Lorem ipsum dolor sit amet consecutor. Lorem ipsum dolor sit amet consecutor. Lorem ipsum dolor sit amet consecutor. Lorem ipsum dolor sit amet consecutor. Lorem ipsum dolor sit amet consecutor. Lorem ipsum dolor sit amet consecutor. Lorem ipsum dolor sit amet consecutor. Lorem ipsum dolor sit amet consecutor. Lorem ipsum dolor sit amet consecutor. Lorem ipsum dolor sit amet consecutor. Lorem ipsum dolor sit amet consecutor. Lorem ipsum dolor sit amet consecutor. Lorem ipsum dolor sit amet consecutor. Lorem ipsum dolor sit amet consecutor.</p>
  </article>
  <div class="entry-rule"></div>
  <article class="entry entry-two">
    <div class="entry-photo" role="img" aria-label="Couple in white robes on a seaside terrace with arches"></div>
    <p>Lorem ipsum dolor sit amet consecutor. Lorem ipsum dolor sit amet consecutor. Lorem ipsum dolor sit amet consecutor. Lorem ipsum dolor sit amet consecutor. Lorem ipsum dolor sit amet consecutor. Lorem ipsum dolor sit amet consecutor. Lorem ipsum dolor sit amet consecutor. Lorem ipsum dolor sit amet consecutor. Lorem ipsum dolor sit amet consecutor. Lorem ipsum dolor sit amet consecutor. Lorem ipsum dolor sit amet consecutor. Lorem ipsum dolor sit amet consecutor. Lorem ipsum dolor sit amet consecutor. Lorem ipsum dolor sit amet consecutor. Lorem ipsum dolor sit amet consecutor. Lorem ipsum dolor sit amet consecutor. Lorem ipsum dolor sit amet consecutor. Lorem ipsum dolor sit amet consecutor. Lorem ipsum dolor sit amet consecutor. Lorem ipsum dolor sit amet consecutor. Lorem ipsum dolor sit amet consecutor. Lorem ipsum dolor sit amet consecutor. Lorem ipsum dolor sit amet consecutor. Lorem ipsum dolor sit amet consecutor. Lorem ipsum dolor sit amet consecutor.</p>
  </article>
</main>

<footer class="site-footer">
  <div class="social" aria-label="Social links">
    <span class="s1"></span><span class="s2"></span><span class="s3"></span>
  </div>
  <p class="copyright">Copyright ©2010 Corvella. All Rights Reserved</p>
  <div class="footer-brand"><span class="brand-dot"></span>Corvella</div>
</footer>
</body>
</html>
```